Animal Eye Clinic needs a Business card

We are a new veterinary ophthalmology practice (Ridgeline Pet Vision Care) and we need a business card designed. We only see animal eyes - we are not a regular veterinary clinic. We already have a logo. We are looking for a professional, good looking business card to hand out to our clients. We are looking for something simple but professional and contemporary. Our logo is likely the only picture/graphic that needs to be on the card.
Updates

Contact Information for Business Card

Delia Vossman, BSc, DVM, MSc, DipACVO
Veterinary Ophthalmologist

Phone: 250.418.3927
Email: ridgelinepetvisioncare@mailbox-example.net
Website: ridgelinepetvisioncare-example.net
Address: 1874 Thornbury Rd
Kelowna, BC, V1X 4M9

Colors

Designer to choose colors to be used in the design.

Requirements
Must have
• Our logo (attached)

```html
<!DOCTYPE html>
<html lang="en">
<head>
<meta charset="utf-8">
<title>Ridgeline Pet Vision Care – Business Card</title>
<link rel="stylesheet" href="https://fonts.googleapis.com/css2?family=Montserrat:wght@700;800&family=Roboto:wght@400;500&display=swap">
<style>
  :root {
    --stage: #2b2b2b;
    --card: #1c1c1c;
    --teal: #1497a9;
    --grey: #8c8c8c;
    --grey-dark: #6f6f6f;
  }
  html, body {
    margin: 0;
    width: 1200px;
    height: 895px;
    overflow: hidden;
    background: var(--stage);
    font-family: "Roboto", Arial, sans-serif;
  }
  .canvas {
    position: relative;
    width: 1200px;
    height: 895px;
  }
  .card {
    position: absolute;
    width: 640px;
    height: 366px;
    background: var(--card);
    box-shadow: 0 14px 30px rgba(0,0,0,.45);
    overflow: hidden;
  }
  .card--front { left: 70px; top: 70px; }
  .card--back  { left: 490px; top: 459px; }

  /* front */
  .brand {
    position: absolute;
    left: 70px;
    top: 132px;
    display: flex;
    align-items: center;
    gap: 18px;
  }
  .brand__mark {
    width: 62px;
    height: 62px;
    border-radius: 50%;
    background: var(--teal);
    flex: none;
  }
  .brand__name {
    font-family: "Montserrat", Arial, sans-serif;
    font-weight: 800;
    color: var(--teal);
    font-size: 30px;
    line-height: 1.05;
    text-transform: uppercase;
    letter-spacing: .5px;
  }
  .front__web {
    position: absolute;
    left: 150px;
    top: 248px;
    font-size: 14px;
    letter-spacing: .8px;
    color: var(--grey);
  }
  .front__web span { color: var(--teal); }

  /* back */
  .back__brand {
    position: absolute;
    left: 70px;
    top: 120px;
    width: 180px;
    display: flex;
    flex-direction: column;
    align-items: center;
    gap: 14px;
  }
  .back__brand .brand__mark { width: 110px; height: 110px; }
  .back__brand .brand__name { font-size: 17px; text-align: center; }

  .contact {
    position: absolute;
    left: 300px;
    top: 70px;
    width: 320px;
    color: var(--grey);
    font-size: 13px;
    line-height: 1.3;
  }
  .contact__name {
    font-family: "Montserrat", Arial, sans-serif;
    font-weight: 800;
    color: var(--teal);
    font-size: 25px;
    text-transform: uppercase;
    margin: 0 0 4px;
    line-height: 1;
  }
  .contact__role { margin: 0 0 16px; }
  .contact__practice { color: var(--teal); font-weight: 500; }
  .contact__address { margin: 0 0 16px; }
  .contact__list { list-style: none; margin: 0; padding: 0; }
  .contact__list li {
    display: flex;
    align-items: center;
    gap: 8px;
    margin-bottom: 3px;
    font-size: 12px;
    white-space: nowrap;
  }
  .contact__list svg { width: 12px; height: 12px; flex: none; fill: var(--teal); }
  .contact__list span.accent { color: var(--teal); }
</style>
</head>
<body>
<div class="canvas">

  <section class="card card--front" aria-label="Card front">
    <div class="brand">
      <div class="brand__mark"></div>
      <div class="brand__name">Ridgeline<br>Pet Vision Care</div>
    </div>
    <p class="front__web">www.<span>ridgelinepetvisioncare-example</span>.net</p>
  </section>

  <section class="card card--back" aria-label="Card back">
    <div class="back__brand">
      <div class="brand__mark"></div>
      <div class="brand__name">Ridgeline Pet Vision Care</div>
    </div>

    <div class="contact">
      <h1 class="contact__name">Delia Vossman</h1>
      <p class="contact__role">BSc, DVM, MSc, DipACVO<br>Veterinary Ophthalmologist</p>
      <p class="contact__address">
        <span class="contact__practice">Ridgeline Pet Vision Care</span><br>
        1874 Thornbury Rd<br>
        Kelowna, BC, V1X 4M9
      </p>
      <ul class="contact__list">
        <li>
          <svg viewBox="0 0 24 24" aria-hidden="true"><path d="M6.6 10.8a15.1 15.1 0 0 0 6.6 6.6l2.2-2.2a1 1 0 0 1 1-.25 11.4 11.4 0 0 0 3.6.57 1 1 0 0 1 1 1V20a1 1 0 0 1-1 1A17 17 0 0 1 3 4a1 1 0 0 1 1-1h3.5a1 1 0 0 1 1 1c0 1.25.2 2.45.57 3.57a1 1 0 0 1-.25 1z"/></svg>
          +1 250 418 3927
        </li>
        <li>
          <svg viewBox="0 0 24 24" aria-hidden="true"><path d="M2 5h20v14H2z M2 5l10 8 10-8" fill="none" stroke="#1497a9" stroke-width="2.4"/></svg>
          ridgelinepetvisioncare@mailbox-example.net
        </li>
        <li>
          <svg viewBox="0 0 24 24" aria-hidden="true"><circle cx="12" cy="12" r="9.5" fill="none" stroke="#1497a9" stroke-width="2"/><path d="M2.5 12h19M12 2.5c3 3 3 16 0 19M12 2.5c-3 3-3 16 0 19" fill="none" stroke="#1497a9" stroke-width="1.6"/></svg>
          www.<span class="accent">ridgelinepetvisioncare-example</span>.net
        </li>
      </ul>
    </div>
  </section>

</div>
</body>
</html>
```